Oven Cleaning flyer design

Hi there,
I need help designing a letterbox flyer. It needs to be DL size.
I have attached a rough design made with Chat GPT.
Would like back and front, have my business colors.
Please find attached mock up of what I would roughly like.
Also find attached logo.
Thank you

Target Market(s)

Home owners over 40

Industry/Entity Type

Cleaning

Requirements
Must have
• Logo, before after of oven, brand colors

```html
<!DOCTYPE html>
<html lang="en">
<head>
<meta charset="utf-8">
<title>Gleam Oven Care – DL Flyer Front and Back</title>
<link rel="stylesheet" href="https://fonts.googleapis.com/css2?family=Archivo+Black&family=Poppins:wght@400;500;600;800&display=swap">
<style>
  :root {
    --teal: #2fb9c4;
    --teal-light: #5fd0d8;
    --ink: #111213;
    --white: #ffffff;
    --page: #ecebe8;
    --muted: #c9d6d8;
  }
  * { box-sizing: border-box; margin: 0; padding: 0; }
  html, body { width: 1200px; height: 844px; overflow: hidden; background: var(--page); }
  body { position: relative; font-family: "Poppins", sans-serif; color: var(--ink); }

  .flyer {
    position: absolute; top: 42px; width: 362px; height: 760px;
    overflow: hidden; background: var(--white);
    box-shadow: 0 6px 22px rgba(0,0,0,.18);
  }
  .flyer--front { left: 200px; }
  .flyer--back { left: 638px; }
  .flyer__bg { position: absolute; inset: 0; width: 100%; height: 100%; }

  .brand {
    position: absolute; top: 46px; left: 0; width: 100%;
    display: flex; align-items: center; justify-content: center; gap: 10px;
  }
  .brand__dot { width: 34px; height: 34px; border-radius: 50%; background: var(--teal); }
  .brand__name { font-family: "Poppins", sans-serif; font-weight: 800; font-size: 26px; color: var(--teal); letter-spacing: .5px; }

  .headline {
    position: absolute; top: 118px; left: 0; width: 100%;
    text-align: center; font-family: "Archivo Black", sans-serif;
    font-size: 27px; line-height: 1.05; text-transform: uppercase;
  }
  .headline .accent { color: var(--teal); }
  .intro {
    position: absolute; top: 188px; left: 28px; right: 28px;
    text-align: center; font-size: 11px; font-weight: 500; line-height: 1.35;
  }

  .before-after {
    position: absolute; top: 268px; left: -70px; width: 502px; height: 330px;
    border-radius: 50%; overflow: hidden;
    background: linear-gradient(90deg, #2a2622 0%, #6b5430 28%, #8a7a5c 48%, #b9bcbd 52%, #d7d9da 75%, #4a4d50 100%);
  }
  .before-after__split { position: absolute; left: 249px; top: 0; width: 5px; height: 100%; background: var(--white); }
  .tag {
    position: absolute; top: 308px; background: var(--teal); color: var(--white);
    font-family: "Archivo Black", sans-serif; font-size: 13px; letter-spacing: 1px;
    padding: 3px 14px;
  }
  .tag--before { left: 64px; }
  .tag--after { left: 190px; top: 334px; }

  .cta {
    position: absolute; top: 612px; left: 0; width: 100%;
    text-align: center; color: var(--white);
    font-family: "Archivo Black", sans-serif; font-size: 15px; line-height: 1.2; text-transform: uppercase;
  }
  .phone {
    position: absolute; left: 0; width: 100%;
    display: flex; align-items: center; justify-content: center; gap: 8px;
    font-family: "Archivo Black", sans-serif; font-size: 30px; color: var(--teal); letter-spacing: .5px;
  }
  .phone__icon { width: 30px; height: 30px; }
  .web {
    position: absolute; left: 0; width: 100%;
    display: flex; align-items: center; justify-content: center; gap: 6px;
    font-size: 14px; color: var(--white);
  }
  .web__icon { width: 12px; height: 12px; }
  .flyer--front .phone { top: 660px; }
  .flyer--front .web { top: 708px; }

  .why {
    position: absolute; top: 112px; left: 0; width: 100%;
    text-align: center; font-family: "Archivo Black", sans-serif;
    font-size: 21px; line-height: 1.1; text-transform: uppercase;
  }
  .why .accent { color: var(--teal); }
  .why-text {
    position: absolute; top: 170px; left: 26px; right: 26px;
    text-align: center; font-size: 11px; font-weight: 500; line-height: 1.4;
  }
  .offer {
    position: absolute; top: 296px; left: -40px; width: 442px; height: 168px;
    border-radius: 50%; background: var(--teal);
    display: flex; flex-direction: column; align-items: center; justify-content: center;
    font-family: "Archivo Black", sans-serif; text-transform: uppercase; text-align: center;
  }
  .offer__lead, .offer__tail { color: var(--white); font-size: 15px; letter-spacing: .5px; }
  .offer__amount { color: var(--ink); font-size: 54px; line-height: 1; margin: 2px 0; }

  .features {
    position: absolute; top: 486px; left: 14px; right: 14px;
    display: flex; justify-content: space-between;
  }
  .feature {
    flex: 1; display: flex; flex-direction: column; align-items: center; gap: 6px;
    color: var(--white); font-size: 11px; font-weight: 600; text-align: center; line-height: 1.2;
  }
  .feature + .feature { border-left: 1px solid #55595c; }
  .feature__icon { width: 28px; height: 28px; }
  .flyer--back .phone { top: 588px; }
  .flyer--back .web { top: 636px; }
  .services {
    position: absolute; top: 680px; left: 0; width: 100%; height: 62px;
    background: var(--teal); color: var(--white);
    display: flex; flex-direction: column; align-items: center; justify-content: center;
    font-family: "Poppins", sans-serif; font-weight: 800; font-size: 15px; line-height: 1.2;
  }
</style>
</head>
<body>

<!-- Front -->
<section class="flyer flyer--front" aria-label="Flyer front">
  <svg class="flyer__bg" viewBox="0 0 362 760" aria-hidden="true">
    <rect width="362" height="760" fill="var(--white)"/>
    <path d="M0 0 H110 C60 30 30 50 0 60 Z" fill="var(--teal)"/>
    <path d="M362 0 V70 C300 95 250 105 200 108 C270 80 320 40 340 0 Z" fill="var(--teal-light)"/>
    <path d="M0 34 C70 100 230 118 362 70" stroke="var(--teal)" stroke-width="4" fill="none"/>
    <path d="M0 478 C110 560 260 570 362 520 V760 H0 Z" fill="var(--ink)"/>
    <path d="M0 262 C110 236 250 240 362 280" stroke="var(--teal)" stroke-width="9" fill="none"/>
    <path d="M0 560 C120 630 270 630 362 590" stroke="var(--teal)" stroke-width="7" fill="none"/>
  </svg>

  <div class="brand"><span class="brand__dot"></span><span class="brand__name">Gleam Oven Care</span></div>

  <h1 class="headline">Bring your <span class="accent">oven</span><br>back to <span class="accent">life</span></h1>
  <p class="intro">Professional, non-caustic oven cleaning that removes built-up grease, smoke, and burnt grime – leaving your oven looking fresh again.</p>

  <div class="before-after" role="img" aria-label="Before and after photo of an open oven: greasy glass door on the left, clean glass door on the right">
    <span class="before-after__split"></span>
  </div>
  <span class="tag tag--before">BEFORE</span>
  <span class="tag tag--after">AFTER</span>

  <p class="cta">Call now for<br>fast, professional service</p>
  <div class="phone">
    <svg class="phone__icon" viewBox="0 0 30 30" aria-hidden="true"><rect width="30" height="30" rx="7" fill="var(--teal)"/><path d="M10 7 L13 11 L11 13 C12 16 14 18 17 19 L19 17 L23 20 L21 23 C14 23 7 16 7 9 Z" fill="var(--ink)"/></svg>
    <span>0400 582 913</span>
  </div>
  <div class="web">
    <svg class="web__icon" viewBox="0 0 12 12" aria-hidden="true"><circle cx="6" cy="6" r="5.5" fill="var(--white)"/><path d="M0.5 6 H11.5 M6 0.5 C3 3 3 9 6 11.5 M6 0.5 C9 3 9 9 6 11.5" stroke="var(--ink)" stroke-width=".8" fill="none"/></svg>
    <span>gleamovencare.com.au</span>
  </div>
</section>

<!-- Back -->
<section class="flyer flyer--back" aria-label="Flyer back">
  <svg class="flyer__bg" viewBox="0 0 362 760" aria-hidden="true">
    <rect width="362" height="760" fill="var(--white)"/>
    <path d="M0 0 H110 C60 30 30 50 0 60 Z" fill="var(--teal)"/>
    <path d="M362 0 V70 C300 95 250 105 200 108 C270 80 320 40 340 0 Z" fill="var(--teal-light)"/>
    <path d="M0 34 C70 100 230 118 362 70" stroke="var(--teal)" stroke-width="4" fill="none"/>
    <path d="M0 420 C110 500 260 500 362 440 V760 H0 Z" fill="var(--ink)"/>
    <path d="M0 282 C120 262 260 268 362 300" stroke="var(--teal)" stroke-width="6" fill="none"/>
  </svg>

  <div class="brand"><span class="brand__dot"></span><span class="brand__name">Gleam Oven Care</span></div>

  <h2 class="why">Why choose<br><span class="accent">Gleam Oven Care?</span></h2>
  <p class="why-text">We're a local family business providing professional, non-caustic oven cleaning across Sunshine Coast. Using specialized equipment and proven cleaning methods, we remove heavy grease, carbon build-up, smoke residue, restoring your oven safely and effectively.</p>

  <div class="offer">
    <span class="offer__lead">Mention this flyer for</span>
    <span class="offer__amount">$10 OFF</span>
    <span class="offer__tail">Your first clean</span>
  </div>

  <div class="features">
    <div class="feature">
      <svg class="feature__icon" viewBox="0 0 28 28" aria-hidden="true"><circle cx="14" cy="14" r="12" stroke="var(--teal)" stroke-width="2" fill="none"/><path d="M8 14 L12 18 L20 10" stroke="var(--teal)" stroke-width="2.2" fill="none"/></svg>
      <span>Reliable<br>Service</span>
    </div>
    <div class="feature">
      <svg class="feature__icon" viewBox="0 0 28 28" aria-hidden="true"><circle cx="14" cy="14" r="12" stroke="var(--teal)" stroke-width="2" fill="none"/><path d="M14 21 C8 17 9 10 14 6 C19 10 20 17 14 21 Z M14 21 V11" stroke="var(--teal)" stroke-width="1.8" fill="none"/></svg>
      <span>Non-Caustic<br>Cleaning</span>
    </div>
    <div class="feature">
      <svg class="feature__icon" viewBox="0 0 28 28" aria-hidden="true"><path d="M14 3 L17 10 L25 11 L19 16 L21 24 L14 20 L7 24 L9 16 L3 11 L11 10 Z" stroke="var(--teal)" stroke-width="1.8" fill="none"/></svg>
      <span>Satisfaction<br>Guaranteed</span>
    </div>
  </div>

  <div class="phone">
    <svg class="phone__icon" viewBox="0 0 30 30" aria-hidden="true"><rect width="30" height="30" rx="7" fill="var(--teal)"/><path d="M10 7 L13 11 L11 13 C12 16 14 18 17 19 L19 17 L23 20 L21 23 C14 23 7 16 7 9 Z" fill="var(--ink)"/></svg>
    <span>0400 582 913</span>
  </div>
  <div class="web">
    <svg class="web__icon" viewBox="0 0 12 12" aria-hidden="true"><circle cx="6" cy="6" r="5.5" fill="var(--white)"/><path d="M0.5 6 H11.5 M6 0.5 C3 3 3 9 6 11.5 M6 0.5 C9 3 9 9 6 11.5" stroke="var(--ink)" stroke-width=".8" fill="none"/></svg>
    <span>gleamovencare.com.au</span>
  </div>

  <div class="services">
    <span>We also clean</span>
    <span>cooktops, rangehoods and BBQs</span>
  </div>
</section>

</body>
</html>
```